Start up Dialysis Clinic needs its first website - Velmira Health

Create a visually appealing and user-friendly website for Velmira Health, a dialysis clinic located in Mt. Irvine, Tobago. The website should effectively communicate our services to local, regional, and international patients, providing essential information and fostering trust and engagement..
Key Goals:

1. Informative: Provide comprehensive information about our services, facility, and team.
2. User-Friendly: Ensure the website is easy to navigate, with a clear structure and accessible content.
3. Engaging: Create a visually appealing design that reflects the professionalism and care of Velmira Health.
4. Responsive: Ensure the website is fully responsive and performs well on all devices, including desktops, tablets, and smartphones.
5. Trust-Building: Include testimonials, credentials, and patient resources to build trust with potential patients.
Scope of Work:

1. Home Page: An inviting and informative landing page that provides an overview of our clinic, mission, and services. Include a call to action for more information and contact details.
2. About Us: A detailed page about Velmira Health, including our mission, vision, team, and facility tour.
3. Services: A comprehensive page describing the dialysis services we offer, including Hemodialysis, Peritoneal Dialysis, and Home Hemodialysis.
4. Patient Information: A resourceful section with guides for new patients, FAQs, insurance and billing information, and downloadable forms.
5. Resources: Educational content about kidney health, dialysis options, diet and nutrition tips, and support groups.
6. Contact Us: A contact page with our address, phone number, email, office hours, a contact form, and a map.

```html
<!DOCTYPE html>
<html lang="en">
<head>
<meta charset="utf-8">
<title>Velmira Health – Dialysis Clinic</title>
<link href="https://fonts.googleapis.com/css2?family=Outfit:wght@400;500;600;700&family=Nunito+Sans:wght@400;600;700&display=swap" rel="stylesheet">
<style>
:root{
  --blue:#3f6fb6;
  --blue-dark:#2f5a9c;
  --footer:#4b7cc2;
  --green:#6b9a3c;
  --green-bar:#6e9b44;
  --ink:#1c1c1c;
  --text:#555c63;
  --muted:#8a9096;
  --pale:#e4f0f4;
  --field:#f1f2f4;
  --white:#fff;
}
*{margin:0;padding:0;box-sizing:border-box}
html,body{width:1200px;height:4139px;overflow:hidden}
body{position:relative;background:var(--white);font-family:"Nunito Sans",sans-serif;color:var(--text)}
.abs{position:absolute}
.h-font{font-family:"Outfit",sans-serif}
.btn{position:absolute;display:flex;align-items:center;justify-content:center;color:#fff;font-weight:700;font-size:13px;letter-spacing:.4px;text-transform:uppercase}
.btn-blue{background:var(--blue)}
.btn-green{background:var(--green)}

/* top bar */
.topbar{position:absolute;left:307px;top:0;width:893px;height:48px;background:var(--green-bar);color:#fff;font-size:13px}
.topbar .item{position:absolute;top:0;height:48px;display:flex;align-items:center;gap:10px}
.icon-box{width:22px;height:22px;border-radius:5px;background:#fff;display:flex;align-items:center;justify-content:center}
.soc{width:17px;height:17px;background:#fff;border-radius:3px;display:inline-block}
.brand-box{position:absolute;left:103px;top:0;width:204px;height:188px;background:#fff;box-shadow:0 2px 8px rgba(0,0,0,.08);display:flex;flex-direction:column;align-items:center;justify-content:center;gap:12px;z-index:3}
.brand-mark{width:62px;height:62px;background:var(--blue)}
.brand-name{font-family:"Outfit",sans-serif;font-weight:600;color:var(--blue);font-size:26px;line-height:1;text-align:center;letter-spacing:1px}
.nav{position:absolute;left:0;top:48px;width:1200px;height:68px;background:#fff}
.nav a{position:absolute;top:28px;font-size:13.5px;color:#333;text-decoration:none}
.nav a.active{color:var(--blue)}
.nav a.active::after{content:"";position:absolute;left:-2px;right:-2px;bottom:-10px;height:3px;background:var(--green)}

/* hero */
.hero{position:absolute;left:0;top:116px;width:1200px;height:551px;background:linear-gradient(90deg,#dbeaf0 0%,#e8f2f5 40%,#eef4f7 100%)}
.hero-photo{position:absolute;left:503px;top:0;width:697px;height:551px;background:linear-gradient(120deg,#e2edf2,#cfdfe8 55%,#bfd2de)}
.hero-welcome{left:112px;top:270px;font-size:26px;color:#222}
.hero-title{left:108px;top:322px;font-family:"Outfit",sans-serif;font-weight:700;font-size:74px;color:var(--blue);letter-spacing:1px;line-height:1}
.hero-sub{left:110px;top:412px;font-family:"Outfit",sans-serif;font-weight:600;font-size:50px;color:var(--green);letter-spacing:2px;line-height:1}

/* about */
.photo{position:absolute}
.sec-title{position:absolute;font-family:"Outfit",sans-serif;font-weight:700;color:var(--ink)}
.sec-title span{color:var(--blue)}
.about-text{left:643px;top:810px;width:440px;font-size:12.5px;line-height:22px;color:var(--muted)}
.tab{position:absolute;top:928px;height:38px;background:#eef0f2;color:#333;font-size:13.5px;display:flex;align-items:center;justify-content:center}
.tab.on{background:var(--blue);color:#fff;font-weight:600}
.tab.on::after{content:"";position:absolute;left:50%;bottom:-7px;margin-left:-6px;border:6px solid transparent;border-bottom:0;border-top:7px solid var(--blue)}
.check{position:absolute;font-size:13px;color:#333;display:flex;align-items:center;gap:12px}
.tick{width:15px;height:15px;border-radius:50%;background:var(--blue);display:flex;align-items:center;justify-content:center}

/* services */
.services{position:absolute;left:0;top:1261px;width:1200px;height:647px;background:linear-gradient(180deg,#e3f0f4,#eaf3f6)}
.svc{position:absolute;top:1438px;width:312px;height:372px;background:#fff;text-align:center}
.svc .circle{position:absolute;left:106px;top:40px;width:100px;height:100px;border-radius:50%;background:#dff0f1}
.svc .num{position:absolute;left:14px;top:20px;font-family:"Outfit",sans-serif;font-size:64px;color:rgba(255,255,255,.35);font-weight:500}
.svc h3{position:absolute;left:0;right:0;top:160px;font-family:"Outfit",sans-serif;font-weight:600;font-size:23px;color:var(--ink)}
.svc p{position:absolute;left:34px;right:34px;top:210px;font-size:12.5px;line-height:24px;color:var(--muted)}
.svc .ghost{position:absolute;left:0;right:0;top:208px;font-family:"Outfit",sans-serif;font-size:64px;color:rgba(0,0,0,.05)}
.svc .line{position:absolute;left:0;right:0;bottom:-4px;height:4px;background:var(--blue)}
.svc .go{position:absolute;left:130px;bottom:-28px;width:52px;height:52px;border-radius:50%;background:var(--green);display:flex;align-items:center;justify-content:center;z-index:2}
.svc.active{background:var(--blue)}
.svc.active h3,.svc.active p{color:#fff}
.svc.active .go{background:#fff}

/* team */
.member{position:absolute;top:2080px;width:236px;height:297px;background:#fff;box-shadow:0 2px 10px rgba(0,0,0,.12)}
.member .pic{position:absolute;left:10px;top:10px;width:216px;height:207px;background:linear-gradient(180deg,#eef1f4,#dfe4ea)}
.member .name{position:absolute;left:11px;top:234px;font-size:14px;color:var(--blue)}
.member .role{position:absolute;left:11px;top:259px;font-size:12px;color:#555}
.member .plus{position:absolute;left:196px;top:250px;width:24px;height:24px;border-radius:50%;background:var(--green);display:flex;align-items:center;justify-content:center}

/* testimonials */
.reviews{position:absolute;left:0;top:2565px;width:1200px;height:415px;background:linear-gradient(180deg,#e6f1f4,#edf5f7)}
.avatar{position:absolute;width:80px;height:80px;border-radius:50%;background:linear-gradient(160deg,#d6dde2,#b9c4cc)}
.rev-name{position:absolute;font-weight:700;font-size:16px;color:var(--green)}
.rev-role{position:absolute;font-size:11px;color:#666}
.stars{position:absolute;font-size:11px;color:#f2a31b;letter-spacing:1px}
.rev-text{position:absolute;width:438px;font-size:12.5px;line-height:24px;color:#333;text-align:justify}
.arrow-dot{position:absolute;width:24px;height:24px;border-radius:50%;background:#d5dcdf;display:flex;align-items:center;justify-content:center}

/* appointment */
.booking{position:absolute;left:111px;top:3062px;width:978px;height:535px;background:#fff;box-shadow:0 2px 14px rgba(0,0,0,.08)}
.field{position:absolute;height:44px;background:var(--field);font-size:12.5px;color:#555;display:flex;align-items:center;padding-left:20px}

/* footer */
.footer{position:absolute;left:0;top:3685px;width:1200px;height:403px;background:var(--footer);color:#fff}
.footer .hd{position:absolute;font-family:"Outfit",sans-serif;font-weight:500;font-size:21px}
.footer .lk{position:absolute;font-size:12.5px;display:flex;align-items:center;gap:10px}
.vline{position:absolute;width:1px;background:rgba(255,255,255,.6)}
.copy{position:absolute;left:0;top:4088px;width:1200px;height:51px;background:var(--green-bar);color:#fff;font-size:12.5px;display:flex;align-items:center;justify-content:center}
</style>
</head>
<body>

<!-- header -->
<div class="brand-box">
  <div class="brand-mark"></div>
  <div class="brand-name">VELMIRA<br>HEALTH</div>
</div>
<div class="topbar">
  <div class="item" style="left:24px">
    <span class="icon-box"><svg width="13" height="13" viewBox="0 0 24 24"><path d="M6.6 10.8a15 15 0 006.6 6.6l2.2-2.2c.3-.3.7-.4 1-.2 1.1.4 2.3.6 3.6.6.6 0 1 .4 1 1V20c0 .6-.4 1-1 1A17 17 0 013 4c0-.6.4-1 1-1h3.5c.6 0 1 .4 1 1 0 1.3.2 2.5.6 3.6.1.3 0 .7-.2 1z" fill="#6e9b44"/></svg></span>
    <span>+1 868 555 0142</span>
  </div>
  <div class="item" style="left:232px">
    <span class="icon-box"><svg width="13" height="11" viewBox="0 0 24 18"><rect x="1" y="1" width="22" height="16" fill="none" stroke="#6e9b44" stroke-width="2"/><path d="M1 1l11 9 11-9" fill="none" stroke="#6e9b44" stroke-width="2"/></svg></span>
    <span>info@velmirahealth.tt</span>
  </div>
  <div class="item" style="left:470px;gap:7px">
    <svg width="20" height="20" viewBox="0 0 24 24" fill="none" stroke="#fff" stroke-width="1.6"><circle cx="12" cy="12" r="10"/><path d="M2 12h20M12 2c3 3 3 17 0 20M12 2c-3 3-3 17 0 20"/></svg>
    <span>Eng</span>
    <svg width="14" height="10" viewBox="0 0 14 10"><path d="M1 2l6 6 6-6" fill="none" stroke="#fff" stroke-width="1.8"/></svg>
  </div>
  <div class="item" style="left:616px;gap:5px">
    <span style="margin-right:6px">Follow Us :</span>
    <span class="soc"></span><span class="soc"></span><span class="soc"></span><span class="soc"></span>
  </div>
</div>
<nav class="nav">
  <a class="active" style="left:400px">Home</a>
  <a style="left:464px">About Us</a>
  <a style="left:549px">Services</a>
  <a style="left:628px">Patient Information</a>
  <a style="left:779px">Resources</a>
  <span class="btn btn-blue" style="left:953px;top:15px;width:136px;height:43px">Contact Us</span>
</nav>

<!-- hero -->
<section class="hero">
  <div class="hero-photo" role="img" aria-label="Two smiling doctors in white coats reviewing a tablet"></div>
</section>
<div class="abs hero-welcome">Welcome To</div>
<div class="abs hero-title">VELMIRA</div>
<div class="abs hero-sub">HEALTH</div>
<span class="btn btn-blue" style="left:111px;top:483px;width:136px;height:44px">Get Started</span>
<span class="btn btn-green" style="left:254px;top:483px;width:201px;height:44px">Book An Appointment</span>

<!-- about -->
<div class="photo" style="left:111px;top:752px;width:368px;height:364px;background:linear-gradient(135deg,#e6e7e9,#c9ccd0 60%,#b4b8bd)" role="img" aria-label="Nurse attending a patient seated in a dialysis chair"></div>
<div class="photo" style="left:345px;top:918px;width:236px;height:252px;background:#fff"></div>
<div class="photo" style="left:345px;top:922px;width:232px;height:244px;background:radial-gradient(circle at 50% 45%,#b9e6ec,#8fd2dc 70%)" role="img" aria-label="Sculpted kidney model on a turquoise background"></div>

<div class="sec-title" style="left:643px;top:748px;font-size:44px">About <span>Us</span></div>
<p class="abs about-text">Lorem ipsum dolor sit amet, consectetur adipiscing elit, sed do eiusmod tempor incididunt ut labore et dolore magna aliqua. Ut enim ad minim veniam, quis nostrud exercitation ullamco laboris nisi ut aliquip ex ea commodo consequat.</p>
<div class="tab on" style="left:641px;width:125px">Our Mission</div>
<div class="tab" style="left:774px;width:124px">Our Vision</div>
<div class="tab" style="left:908px;width:123px">Our Team</div>
<div class="check" style="left:642px;top:999px"><span class="tick"><svg width="9" height="8" viewBox="0 0 10 8"><path d="M1 4l3 3 5-6" fill="none" stroke="#fff" stroke-width="1.8"/></svg></span>Sed ut perspiciatis unde</div>
<div class="check" style="left:642px;top:1034px"><span class="tick"><svg width="9" height="8" viewBox="0 0 10 8"><path d="M1 4l3 3 5-6" fill="none" stroke="#fff" stroke-width="1.8"/></svg></span>unde omnis iste sit</div>
<div class="check" style="left:872px;top:999px"><span class="tick"><svg width="9" height="8" viewBox="0 0 10 8"><path d="M1 4l3 3 5-6" fill="none" stroke="#fff" stroke-width="1.8"/></svg></span>Sed ut perspiciatis unde</div>
<div class="check" style="left:872px;top:1034px"><span class="tick"><svg width="9" height="8" viewBox="0 0 10 8"><path d="M1 4l3 3 5-6" fill="none" stroke="#fff" stroke-width="1.8"/></svg></span>unde omnis iste natus</div>
<span class="btn btn-green" style="left:639px;top:1087px;width:137px;height:44px">Read More</span>

<!-- services -->
<section class="services"></section>
<div class="sec-title" style="left:0;width:1200px;text-align:center;top:1314px;font-size:46px">Our <span>Services</span></div>
<div class="abs" style="left:0;width:1200px;text-align:center;top:1376px;font-size:14.5px;color:#333">Excepteur sint occaecat cupidatat non proident, sunt in culpa qui officia deserunt</div>

<div class="svc" style="left:117px">
  <div class="circle" role="img" aria-label="Hemodialysis machine illustration"></div>
  <h3>Hemodialysis</h3>
  <div class="ghost">01</div>
  <p>Nemo enim ipsam voluptatem quia voluptas sit aspernatur aut odit aut fugit, sed quia consequuntur magni dolores eos qui ratione voluptatem sequi nesciunt.</p>
  <div class="line"></div>
  <div class="go"><svg width="22" height="16" viewBox="0 0 22 16"><path d="M1 8h19M13 1l7 7-7 7" fill="none" stroke="#fff" stroke-width="1.8"/></svg></div>
</div>
<div class="svc active" style="left:445px">
  <div style="position:absolute;inset:0;background:linear-gradient(180deg,#4a7ac0,#3b69ad)" role="img" aria-label="Faint silhouettes of patients behind the card"></div>
  <div class="num">02</div>
  <div class="circle" style="background:#fff" role="img" aria-label="Peritoneal dialysis care illustration"></div>
  <h3>Peritoneal Dialysis</h3>
  <p style="top:202px;left:34px;right:34px">Nemo enim ipsam voluptatem quia voluptas sit aspernatur aut odit aut fugit, sed quia consequuntur magni dolores eos qui ratione voluptatem sequi nesciunt.</p>
  <div class="go"><svg width="22" height="16" viewBox="0 0 22 16"><path d="M1 8h19M13 1l7 7-7 7" fill="none" stroke="#3f6fb6" stroke-width="1.8"/></svg></div>
</div>
<div class="svc" style="left:773px">
  <div class="circle" role="img" aria-label="Home dialysis equipment illustration"></div>
  <h3>Home Hemodialysis</h3>
  <div class="ghost">03</div>
  <p>Nemo enim ipsam voluptatem quia voluptas sit aspernatur aut odit aut fugit, sed quia consequuntur magni dolores eos qui ratione voluptatem sequi nesciunt.</p>
  <div class="line"></div>
  <div class="go"><svg width="22" height="16" viewBox="0 0 22 16"><path d="M1 8h19M13 1l7 7-7 7" fill="none" stroke="#fff" stroke-width="1.8"/></svg></div>
</div>

<!-- team -->
<div class="sec-title" style="left:0;width:1200px;text-align:center;top:1994px;font-size:46px">Our <span>Team</span></div>
<div class="member" style="left:109px"><div class="pic" role="img" aria-label="Portrait of a female doctor with stethoscope"></div><div class="name">Dr.Amara Lynes</div><div class="role">Peritoneal Dialysist</div><div class="plus"><svg width="12" height="12"><path d="M6 1v10M1 6h10" stroke="#fff" stroke-width="2"/></svg></div></div>
<div class="member" style="left:355px"><div class="pic" role="img" aria-label="Portrait of a senior male doctor holding a laptop"></div><div class="name">Dr.Corvin Hale</div><div class="role">Hemodialysist</div><div class="plus"><svg width="12" height="12"><path d="M6 1v10M1 6h10" stroke="#fff" stroke-width="2"/></svg></div></div>
<div class="member" style="left:601px"><div class="pic" role="img" aria-label="Portrait of a female doctor with arms crossed"></div><div class="name">Dr.Nadia Persad</div><div class="role">Home Hemodialysist</div><div class="plus"><svg width="12" height="12"><path d="M6 1v10M1 6h10" stroke="#fff" stroke-width="2"/></svg></div></div>
<div class="member" style="left:847px"><div class="pic" role="img" aria-label="Portrait of a young male doctor with arms crossed"></div><div class="name">Dr.Tobin Reyes</div><div class="role">Peritoneal Dialysist</div><div class="plus"><svg width="12" height="12"><path d="M6 1v10M1 6h10" stroke="#fff" stroke-width="2"/></svg></div></div>
<span class="btn btn-green" style="left:532px;top:2430px;width:136px;height:45px">View All</span>

<!-- testimonials -->
<section class="reviews"></section>
<div class="sec-title" style="left:0;width:1200px;text-align:center;top:2622px;font-size:46px">What Our <span>Customers Says?</span></div>
<div class="avatar" style="left:117px;top:2733px" role="img" aria-label="Customer portrait"></div>
<div class="rev-name" style="left:217px;top:2747px">Marlon</div>
<div class="rev-role" style="left:217px;top:2771px">Customer</div>
<div class="stars" style="left:217px;top:2786px">★★★★★</div>
<p class="rev-text" style="left:112px;top:2826px">Lorem ipsum dolor sit amet, consectetur adipiscing elit, sed do eiusmod tempor incididunt ut labore et dolore magna aliqua. Ut enim ad minim veniam, quis nostrud exercitation ullamco laboris nisi ut aliquip ex ea commodo consequat.</p>
<div class="abs" style="left:599px;top:2779px;width:2px;height:120px;background:#a9b3b8"></div>
<div class="avatar" style="left:648px;top:2733px" role="img" aria-label="Customer portrait"></div>
<div class="rev-name" style="left:747px;top:2747px">Keisha Daly</div>
<div class="rev-role" style="left:748px;top:2771px">Customer</div>
<div class="stars" style="left:748px;top:2786px">★★★★★</div>
<p class="rev-text" style="left:644px;top:2826px">Lorem ipsum dolor sit amet, consectetur adipiscing elit, sed do eiusmod tempor incididunt ut labore et dolore magna aliqua. Ut enim ad minim veniam, quis nostrud exercitation ullamco laboris nisi ut aliquip ex ea commodo consequat.</p>
<div class="arrow-dot" style="left:36px;top:2834px"><svg width="12" height="10" viewBox="0 0 12 10"><path d="M11 5H1M5 1L1 5l4 4" fill="none" stroke="#fff" stroke-width="1.5"/></svg></div>
<div class="arrow-dot" style="left:1133px;top:2834px"><svg width="12" height="10" viewBox="0 0 12 10"><path d="M1 5h10M7 1l4 4-4 4" fill="none" stroke="#fff" stroke-width="1.5"/></svg></div>

<!-- booking -->
<div class="booking">
  <div style="position:absolute;left:0;top:0;width:446px;height:535px;background:linear-gradient(150deg,#d6e3ef,#9fb9d4 45%,#6f8fb8)" role="img" aria-label="Clinician operating a dialysis machine beside a patient in a treatment bed"></div>
</div>
<div class="sec-title" style="left:596px;top:3120px;font-size:45px">Book An <span>Appointment</span></div>
<div class="field" style="left:596px;top:3198px;width:228px">Firs Name</div>
<div class="field" style="left:835px;top:3198px;width:228px">Last Name</div>
<div class="field" style="left:596px;top:3250px;width:228px">Name</div>
<div class="field" style="left:835px;top:3250px;width:228px">Phonen Nmber</div>
<div class="field" style="left:596px;top:3301px;width:467px">Email Address</div>
<div class="field" style="left:596px;top:3353px;width:467px">Choose Service
  <svg style="position:absolute;right:18px;top:17px" width="14" height="9" viewBox="0 0 14 9"><path d="M1 1l6 6 6-6" fill="none" stroke="#333" stroke-width="1.5"/></svg></div>
<div class="field" style="left:596px;top:3405px;width:228px">Date</div>
<div class="field" style="left:835px;top:3405px;width:228px">Time</div>
<div class="field" style="left:596px;top:3457px;width:467px">Message</div>
<span class="btn btn-green" style="left:607px;top:3520px;width:135px;height:43px">Book Now</span>

<!-- footer -->
<footer class="footer">
  <div class="abs" style="left:133px;top:30px;width:36px;height:36px;border-radius:9px;background:#fff;display:flex;align-items:center;justify-content:center">
    <svg width="20" height="20" viewBox="0 0 24 24"><path d="M6.6 10.8a15 15 0 006.6 6.6l2.2-2.2c.3-.3.7-.4 1-.2 1.1.4 2.3.6 3.6.6.6 0 1 .4 1 1V20c0 .6-.4 1-1 1A17 17 0 013 4c0-.6.4-1 1-1h3.5c.6 0 1 .4 1 1 0 1.3.2 2.5.6 3.6.1.3 0 .7-.2 1z" fill="#4b7cc2"/></svg>
  </div>
  <div class="abs h-font" style="left:194px;top:27px;font-size:17px;font-weight:500">Give Us Call</div>
  <div class="abs" style="left:189px;top:57px;font-size:14px">+1 868 555 0142</div>
  <div class="abs" style="left:466px;top:43px;display:flex;gap:7px"><span class="soc" style="width:22px;height:22px"></span><span class="soc" style="width:22px;height:22px"></span><span class="soc" style="width:22px;height:22px"></span><span class="soc" style="width:22px;height:22px"></span></div>
  <div class="vline" style="left:623px;top:0;height:102px"></div>
  <div class="abs h-font" style="left:655px;top:27px;font-size:17px;font-weight:600;line-height:23px">Join &nbsp;Our<br>Newsletter</div>
  <div class="abs" style="left:776px;top:31px;width:231px;height:45px;background:#fff;color:#333;font-size:12px;display:flex;align-items:center;padding-left:40px">Your Email</div>
  <div class="abs" style="left:1007px;top:31px;width:84px;height:45px;background:var(--green);font-size:13px;font-weight:700;display:flex;align-items:center;justify-content:center">Subscribe</div>
  <div class="abs" style="left:119px;top:102px;width:973px;height:1px;background:rgba(255,255,255,.7)"></div>

  <div class="abs" style="left:112px;top:154px;width:196px;display:flex;flex-direction:column;align-items:center;gap:14px">
    <div style="width:64px;height:64px;background:#fff"></div>
    <div class="h-font" style="font-weight:600;font-size:30px;line-height:1.05;text-align:center;letter-spacing:1px">VELMIRA<br>HEALTH</div>
  </div>

  <div class="hd" style="left:434px;top:142px">Quick Links</div>
  <div class="lk" style="left:445px;top:196px">»&nbsp;Home</div>
  <div class="lk" style="left:445px;top:230px">»&nbsp;About Us</div>
  <div class="lk" style="left:445px;top:266px">»&nbsp;Services</div>
  <div class="lk" style="left:445px;top:300px">»&nbsp;Patient Information</div>
  <div class="lk" style="left:445px;top:334px">»&nbsp;Resources</div>
  <div class="lk" style="left:445px;top:369px">»&nbsp;Contact Us</div>
  <div class="vline" style="left:622px;top:135px;height:238px"></div>

  <div class="hd" style="left:639px;top:142px">Contact Info</div>
  <div class="lk" style="left:643px;top:196px"><svg width="10" height="12" viewBox="0 0 10 13"><path d="M5 0a5 5 0 00-5 5c0 4 5 8 5 8s5-4 5-8a5 5 0 00-5-5zm0 7a2 2 0 110-4 2 2 0 010 4z" fill="#fff"/></svg>Lorem Ipsum, Tobago -437916</div>
  <div class="lk" style="left:643px;top:235px"><svg width="11" height="11" viewBox="0 0 24 24"><path d="M6.6 10.8a15 15 0 006.6 6.6l2.2-2.2c.3-.3.7-.4 1-.2 1.1.4 2.3.6 3.6.6.6 0 1 .4 1 1V20c0 .6-.4 1-1 1A17 17 0 013 4c0-.6.4-1 1-1h3.5c.6 0 1 .4 1 1 0 1.3.2 2.5.6 3.6.1.3 0 .7-.2 1z" fill="#fff"/></svg>+1868 555 0142</div>
  <div class="lk" style="left:643px;top:275px"><svg width="11" height="8" viewBox="0 0 24 18"><rect x="0" y="0" width="24" height="18" fill="#fff"/><path d="M1 1l11 9 11-9" fill="none" stroke="#4b7cc2" stroke-width="2"/></svg>info@velmira.tt</div>
  <div class="vline" style="left:871px;top:135px;height:238px"></div>

  <div class="hd" style="left:908px;top:142px">Help Links</div>
  <div class="lk" style="left:914px;top:196px">»&nbsp;Privacy Policy</div>
  <div class="lk" style="left:914px;top:230px">»&nbsp;Terms &amp; Conditions</div>
  <div class="lk" style="left:914px;top:266px">»&nbsp;Disclaimer</div>
</footer>
<div class="copy">Copyright © 2024 Velmira Health . All rights reserved.</div>

</body>
</html>
```